Lawn Sign For Construction Projects - Brisk Harbor

This contest is for a lawn sign that will be placed in the front yard of recently completed construction projects. The goal here is to have a bold advertising sign that is visible from a vehicle driving past.

We are still deciding on the default size for our sign, we also may use multiple sizes. The two sizes we will more than likely be using are: 18"h x 24"w and 24"h x 36"w.

Preference will be given to designers that submit original designs that tie into our current brand and are either in both the size formats listed above or are easy to scale in photoshop or illustrator.

In the files, you will see our logo and an example of a lawn sign.

Please contact us with any questions or comments you may have!

Thank You,
- The Brisk Harbor Team
Updates

Project Deadline Extended Reason: We Currently to not have any designs worth choosing. Added Monday, March 21, 2016

Industry/Entity Type

Residential Construction

Colors
34a7d8
ffffff
faa54b

Requirements
Nice to have
• 1. The sign must tie into our current branding and color scheme.
• 2. The sign must be clearly visible and readable.
• 3. The sign must include our phone number in readable print.
• 4. Our website written in small print along the bottom of the sign.
• 5. Must mention we install the following products:
• a.) Solar
• b.) Roofing
• c.) Windows
• d.) Artificial Lawn
• e.) Whole House Fans
• f.) Patio Covers

```html
<!DOCTYPE html>
<html lang="en">
<head>
<meta charset="utf-8">
<title>Brisk Harbor Lawn Sign</title>
<link href="https://fonts.googleapis.com/css2?family=Archivo:ital,wght@1,900&family=Exo+2:ital,wght@1,900&family=Montserrat:wght@500;600;700&display=swap" rel="stylesheet">
<style>
  :root {
    --backdrop: #e8ebe6;
    --sign-black: #000000;
    --sign-blue: #1074bd;
    --sign-orange: #ee6a24;
    --brand-orange: #ef7622;
    --arrow-yellow-start: #fff200;
    --arrow-yellow-end: #ffcb08;
    --sign-white: #ffffff;
  }
  html, body {
    margin: 0;
    padding: 0;
    width: 1200px;
    height: 1200px;
    overflow: hidden;
    background: var(--backdrop);
  }
  .lawn-sign {
    display: block;
    width: 1200px;
    height: 1200px;
  }
  .sign-base { fill: var(--sign-black); }
  .contact-band { fill: var(--sign-blue); }
  .arrow-shape { fill: url(#arrowGradient); }
  .brand-mark { fill: none; stroke: var(--sign-blue); stroke-width: 9; }
  .brand-name {
    font-family: "Montserrat", sans-serif;
    font-weight: 600;
    font-size: 64px;
    fill: var(--brand-orange);
  }
  .headline-top {
    font-family: "Exo 2", sans-serif;
    font-style: italic;
    font-weight: 900;
    font-size: 178px;
    fill: var(--sign-black);
  }
  .headline-main {
    font-family: "Archivo", sans-serif;
    font-style: italic;
    font-weight: 900;
    font-size: 312px;
    fill: var(--sign-orange);
  }
  .product-list {
    font-family: "Montserrat", sans-serif;
    font-weight: 700;
    font-size: 30px;
    fill: var(--sign-black);
  }
  .phone-number {
    font-family: "Montserrat", sans-serif;
    font-weight: 500;
    font-size: 104px;
    fill: var(--sign-white);
  }
  .web-address {
    font-family: "Montserrat", sans-serif;
    font-weight: 600;
    font-size: 26px;
    fill: var(--sign-white);
  }
</style>
</head>
<body>
<svg class="lawn-sign" viewBox="0 0 1500 1500" xmlns="http://www.w3.org/2000/svg" role="img" aria-label="Brisk Harbor lawn sign: We've Gone Solar, also roofing, windows, artificial lawn, whole house fans and patio covers">
  <defs>
    <linearGradient id="arrowGradient" x1="0" y1="0" x2="1" y2="0">
      <stop offset="0" stop-color="var(--arrow-yellow-start)"/>
      <stop offset="1" stop-color="var(--arrow-yellow-end)"/>
    </linearGradient>
  </defs>

  <rect class="sign-base" x="100" y="265" width="1295" height="970"/>

  <polygon class="contact-band" points="100,1058 935,1064 945,1235 100,1235"/>
  <polygon class="contact-band" points="1395,768 1395,1235 972,1235"/>

  <polygon class="arrow-shape" points="100,468 1085,468 1115,290 1395,745 955,1210 980,1035 100,1030"/>

  <circle class="brand-mark" cx="270" cy="372" r="58"/>
  <text class="brand-name" x="370" y="398" textLength="515" lengthAdjust="spacingAndGlyphs">BRISK HARBOR</text>

  <text class="headline-top" x="200" y="675" textLength="1000" lengthAdjust="spacingAndGlyphs">We've Gone</text>
  <text class="headline-main" x="172" y="942" textLength="1010" lengthAdjust="spacingAndGlyphs">Solar</text>

  <text class="product-list" x="180" y="1003" textLength="955" lengthAdjust="spacingAndGlyphs">Roofing · Windows · Artificial Lawn · Whole House Fans · Patio Covers</text>

  <text class="phone-number" x="205" y="1185" textLength="668" lengthAdjust="spacingAndGlyphs">044 555 0142</text>
  <text class="web-address" x="1068" y="1187" textLength="277" lengthAdjust="spacingAndGlyphs">www.briskharbor.com</text>
</svg>
</body>
</html>
```